Harborview Estates Business Card for Apartment Buildings

Create business cards for resident managers who run apartment buildings. The audience is the public who are searching for apartment rentals, and current residents who live at the apartment building. Key design element will be incorporating the company logo, however, the logo cannot dominate. The building name and manager name are more important than the logo. Current business card design leaves little room for copy, so we may need to reduce the size on the current card to allow for more space for copy.

Target Market(s)

Adults 18-65 years of age, who are looking for an apartment rental, plus current residents who live at our apartment buildings.

Industry/Entity Type

Property Management

Contact Information for Business Card

A major design element will be use of the company logo. Important property and manager contact information must be part of the design. The size of the logo will need to be reduced to make room for building and manager contact copy.

Font styles to use
Sans Serif

Colors
3176b5
000000
959595
ffffff

Requirements
Must have
• 1) Incorporate the company logo.
• 2) Use the company colors (dark blue, black/grey, over white).
• 3) FEATURE THE BUILDING NAME
• 4) FEATURE THE MANAGER NAME
• 5) The company name is less important than BUILDING and MANAGER
• 6) Manager contact information
• **SEE ATTACHED CREATIVE BRIEF**
Nice to have
• 1) Back of card logo watermark
• 2) Ability to write notes on back of carfd
Should not have
• Avoid letting the company logo dominate the card, the building name and manager are more important than the company logo.

```html
<!DOCTYPE html>
<html lang="en">
<head>
<meta charset="utf-8">
<title>Harborview Estates Business Card</title>
<link href="https://fonts.googleapis.com/css2?family=Roboto+Condensed:wght@500;700&family=Roboto:wght@400;500;700&display=swap" rel="stylesheet">
<style>
  :root {
    --brand-blue: #0f6aa8;
    --brand-blue-light: #2f7db8;
    --charcoal: #46474a;
    --grey-text: #4a4a4a;
    --card-white: #f3f3f3;
    --page-bg: #e6e7e9;
    --white: #ffffff;
  }
  * { margin: 0; padding: 0; box-sizing: border-box; }
  html, body { width: 1200px; height: 960px; overflow: hidden; }
  body {
    background: var(--page-bg);
    position: relative;
    font-family: "Roboto", Arial, sans-serif;
  }
  .card {
    position: absolute;
    width: 600px;
    height: 342px;
    overflow: hidden;
  }
  .card-back {
    left: 322px; top: 108px;
    background: var(--brand-blue);
  }
  .back-name {
    position: absolute;
    left: 0; right: 0; top: 148px;
    text-align: center;
    font-family: "Roboto Condensed", Arial, sans-serif;
    font-weight: 700;
    font-size: 40px;
    color: var(--brand-blue-light);
  }
  .card-front {
    left: 320px; top: 493px;
    background: var(--card-white);
  }
  .company-name {
    position: absolute;
    left: 28px; top: 42px;
    display: flex; align-items: center; gap: 10px;
    font-family: "Roboto Condensed", Arial, sans-serif;
    font-weight: 700;
    font-size: 30px;
    color: var(--brand-blue);
    line-height: 1;
  }
  .company-mark {
    width: 26px; height: 26px; border-radius: 50%;
    background: var(--charcoal);
  }
  .shapes { position: absolute; left: 0; top: 0; }
  .contact-block {
    position: absolute;
    left: 30px; top: 136px;
    color: var(--white);
  }
  .manager-name, .building-name {
    font-family: "Roboto Condensed", Arial, sans-serif;
    font-weight: 700;
    font-size: 24px;
    line-height: 28px;
  }
  .manager-title { font-size: 15px; font-weight: 500; line-height: 19px; }
  .building-name { margin-top: 8px; }
  .address { font-size: 14px; line-height: 17px; }
  .contact-line {
    display: flex; align-items: center; gap: 6px;
    font-size: 14.5px; line-height: 19px;
  }
  .contact-line:first-of-type { margin-top: 12px; }
  .contact-item { display: inline-flex; align-items: center; gap: 6px; margin-right: 4px; }
  .contact-item svg { width: 13px; height: 13px; fill: var(--white); }
  .tagline {
    position: absolute;
    left: 25px; top: 308px;
    font-size: 14px; font-weight: 700;
    color: var(--grey-text);
  }
</style>
</head>
<body>
  <div class="card card-back">
    <div class="back-name">Harborview Estates</div>
  </div>

  <div class="card card-front">
    <div class="company-name"><span class="company-mark"></span>Harborview Estates</div>

    <svg class="shapes" width="600" height="342" viewBox="0 0 600 342">
      <rect x="407" y="211" width="193" height="36" fill="var(--charcoal)"/>
      <polygon points="0,131 348,131 465,300 0,300" fill="var(--brand-blue)"/>
      <line x1="348" y1="131" x2="465" y2="300" stroke="var(--white)" stroke-width="3"/>
    </svg>

    <div class="contact-block">
      <div class="manager-name">Marisol Delgado</div>
      <div class="manager-title">Resident Manager</div>
      <div class="building-name">Cedar Court Apartments</div>
      <div class="address">2485 Linden Avenue, Bayside, CA 90412</div>
      <div class="contact-line">
        <span class="contact-item">
          <svg viewBox="0 0 16 16"><path d="M3 1l3 3-2 2c1 2 3 4 5 5l2-2 3 3-2 3C6 15 1 10 1 3z"/></svg>555-214-3080
        </span>
        <span class="contact-item">
          <svg viewBox="0 0 16 16"><path d="M4 0h8v16H4z M5.5 2v10h5V2z"/></svg>555-214-7761
        </span>
        <span class="contact-item">
          <svg viewBox="0 0 16 16"><path d="M4 1h8v4H4z M1 6h14v6h-2v3H3v-3H1z M5 11v3h6v-3z"/></svg>555-214-9005
        </span>
      </div>
      <div class="contact-line">
        <span class="contact-item">
          <svg viewBox="0 0 16 16"><path d="M1 3h14v10H1z M2 4l6 5 6-5" stroke="#0f6aa8" stroke-width="1"/></svg>marisol@harborviewest.com
        </span>
        <span class="contact-item">
          <svg viewBox="0 0 16 16"><circle cx="8" cy="8" r="7"/><path d="M1 8h14M8 1c-3 4-3 10 0 14M8 1c3 4 3 10 0 14" stroke="#0f6aa8" fill="none"/></svg>harborviewest.com
        </span>
      </div>
    </div>

    <div class="tagline">Multifamily Property Management</div>
  </div>
</body>
</html>
```